Stonebridge Building and Projects business cards

A business card with watermark background (construction work)

Company logo attached

Home improvement projects
House renovations
Bathroom and kitchen renovations
House extensions
New builds and granny flats

Director Omar Haddani
(Phone number)
omar@sbpbuilding.com.au
(Instagram logo) sbp_building

```html
<!DOCTYPE html>
<html lang="en">
<head>
<meta charset="utf-8">
<title>Stonebridge Building and Projects – Business Cards</title>
<link rel="stylesheet" href="https://fonts.googleapis.com/css2?family=Arimo:wght@400;700&display=swap">
<style>
  :root {
    --backdrop: #1c1c1e;
    --brand-blue: #3177b9;
    --card-white: #ffffff;
    --wave-grey: #414245;
    --ink-white: #ffffff;
  }
  * { margin: 0; padding: 0; box-sizing: border-box; }
  html, body {
    width: 1200px; height: 1015px; overflow: hidden;
    background: var(--backdrop);
    font-family: "Arimo", Arial, sans-serif;
  }
  .canvas { position: relative; width: 1200px; height: 1015px; }
  .card {
    position: absolute; width: 540px; height: 310px;
    background: var(--card-white); overflow: hidden;
    box-shadow: 0 18px 40px rgba(0,0,0,.55);
  }
  .card-front { left: 70px; top: 150px; }
  .card-back { left: 590px; top: 555px; }
  .card-art { position: absolute; inset: 0; width: 100%; height: 100%; }

  .service-list {
    position: absolute; left: 34px; top: 40px;
    list-style: none; color: var(--ink-white);
    font-size: 15px; line-height: 24px;
  }
  .service-list li::before {
    content: ""; display: inline-block; width: 7px; height: 7px;
    border-radius: 50%; background: var(--ink-white);
    margin-right: 8px; vertical-align: middle;
  }

  .company-name {
    position: absolute; display: flex; align-items: flex-start; gap: 10px;
    color: var(--brand-blue); font-weight: 700;
    font-size: 22px; line-height: 26px;
  }
  .company-name .mark-square {
    width: 20px; height: 20px; margin-top: 3px;
    background: var(--brand-blue); flex: none;
  }
  .card-front .company-name { right: 28px; top: 112px; }
  .card-back .company-name { left: 48px; top: 52px; }

  .contact-block {
    position: absolute; right: 30px; top: 150px;
    text-align: right; color: var(--ink-white);
  }
  .person-name { font-size: 24px; font-weight: 700; }
  .person-role { font-size: 15px; margin-bottom: 16px; }
  .contact-line {
    display: flex; justify-content: flex-end; align-items: center; gap: 8px;
    font-size: 15px; line-height: 22px;
  }
  .contact-line svg { width: 15px; height: 15px; flex: none; }

  .social-handle {
    position: absolute; left: 34px; bottom: 24px;
    display: flex; align-items: center; gap: 10px;
    color: var(--ink-white); font-size: 16px;
  }
  .social-handle .dot { width: 20px; height: 20px; border-radius: 50%; background: var(--ink-white); }
</style>
</head>
<body>
<main class="canvas">

  <section class="card card-front" aria-label="Business card front">
    <svg class="card-art" viewBox="0 0 540 310" preserveAspectRatio="none" aria-hidden="true">
      <path d="M0 0 H540 V20 C430 18 350 40 300 100 C250 165 170 225 0 250 Z" fill="var(--brand-blue)"/>
      <path d="M540 30 C445 26 365 50 314 110 C262 176 180 236 10 262" fill="none" stroke="var(--brand-blue)" stroke-width="4"/>
      <path d="M540 42 C455 38 380 62 328 122 C278 188 200 240 120 258" fill="none" stroke="var(--wave-grey)" stroke-width="5"/>
    </svg>
    <ul class="service-list">
      <li>Home improvement projects</li>
      <li>Bathroom and kitchen renovations</li>
      <li>House renovations</li>
      <li>House extensions</li>
      <li>New builds and granny flats</li>
    </ul>
    <div class="company-name"><span class="mark-square"></span><span>Stonebridge<br>Building and<br>Projects</span></div>
  </section>

  <section class="card card-back" aria-label="Business card back">
    <svg class="card-art" viewBox="0 0 540 310" preserveAspectRatio="none" aria-hidden="true">
      <path d="M0 310 V268 C170 262 245 245 318 168 C378 106 440 92 540 88 V310 Z" fill="var(--brand-blue)"/>
      <path d="M10 258 C165 252 238 234 306 160 C366 98 430 82 540 78" fill="none" stroke="var(--brand-blue)" stroke-width="4"/>
      <path d="M0 248 C150 244 225 225 292 150 C340 98 380 80 420 76" fill="none" stroke="var(--wave-grey)" stroke-width="5"/>
      <path d="M0 274 C175 268 250 250 322 172 C380 112 442 98 540 94" fill="none" stroke="var(--card-white)" stroke-width="2"/>
    </svg>
    <div class="company-name"><span class="mark-square"></span><span>Stonebridge<br>Building and<br>Projects</span></div>
    <div class="contact-block">
      <div class="person-name">Omar Haddani</div>
      <div class="person-role">Director</div>
      <div class="contact-line"><span>044-987 650 321</span>
        <svg viewBox="0 0 16 16"><path d="M3 1.5l3 .5 1 3.5-1.8 1.2a9 9 0 0 0 4.1 4.1L10.5 9l3.5 1 .5 3-2 1.5C6 14 2 10 1.5 3.5Z" fill="var(--ink-white)"/></svg></div>
      <div class="contact-line"><span>omar@sbpbuilding.com.au</span>
        <svg viewBox="0 0 16 16"><rect x="1" y="3" width="14" height="10" fill="none" stroke="var(--ink-white)" stroke-width="1.6"/><path d="M1 3l7 6 7-6" fill="none" stroke="var(--ink-white)" stroke-width="1.6"/></svg></div>
      <div class="contact-line"><span>www.sbpbuilding.com.au</span>
        <svg viewBox="0 0 16 16"><circle cx="8" cy="8" r="6.5" fill="none" stroke="var(--ink-white)" stroke-width="1.5"/><ellipse cx="8" cy="8" rx="3" ry="6.5" fill="none" stroke="var(--ink-white)" stroke-width="1.2"/><path d="M1.5 8h13" stroke="var(--ink-white)" stroke-width="1.2"/></svg></div>
    </div>
    <div class="social-handle"><span class="dot"></span><span>sbp_building</span></div>
  </section>

</main>
</body>
</html>
```